Business Cards for company that supports physicians that do medical research

Need to create a business card for Qorvel Studies (www.qorvelstudies.example), a company devoted to supporting physicians who conduct medical research. The form of the card should match the message of research and information quest. I have provided the logo of the company as an uploaded file. Designs should be simple and slick aimed at very high end clients.

Target Market(s)

Medical doctors that are also researchers

Industry/Entity Type

Medical

Contact Information for Business Card

Should feature logo and fields for personal info:
Name/title
Phone /email

Font styles to use
Serif
Sans Serif

Requirements
Must have
• Qorvel logo and fields for personal info:
• Name: Bertrand Okonfu
• Title: VP Research and Senior Analyst
• Phone: 555-203-4719
• email: info@qorvelstudies.example
Nice to have
• Interesting cards that I've seen:
• 1- all black/charcoal or very dark background
• 2- Plastic - semi-transparent
• 3- non-standard height-width ratios
• 4- Functional cards -- USB drive incorporated
Should not have
• Too busy; needs to stay very simple

```html
<!DOCTYPE html>
<html lang="en">
<head>
<meta charset="utf-8">
<title>Qorvel Studies — Business Card</title>
<link rel="stylesheet" href="https://fonts.googleapis.com/css2?family=Open+Sans:ital,wght@0,400;0,600;1,400&display=swap">
<style>
  :root {
    --backdrop: #3a3a3a;
    --paper: #f7f7f7;
    --brand-blue: #1b7bbf;
    --brand-green: #4bb549;
    --ink-white: #ffffff;
    --divider: rgba(255,255,255,0.55);
  }
  * { box-sizing: border-box; margin: 0; padding: 0; }
  html, body { width: 1200px; height: 750px; overflow: hidden; }
  body {
    background: var(--backdrop);
    font-family: "Open Sans", sans-serif;
    position: relative;
  }
  .card {
    position: absolute;
    top: 228px;
    width: 461px;
    height: 262px;
    overflow: hidden;
  }
  .card--front { left: 124px; background: var(--paper); }
  .card--back { left: 618px; background: var(--brand-blue); }

  .front-shape { position: absolute; inset: 0; }

  .wordmark {
    position: absolute;
    font-weight: 600;
    white-space: nowrap;
  }
  .card--front .wordmark {
    left: 0; right: 0; top: 58px;
    text-align: center;
    font-size: 32px;
    color: var(--brand-green);
    letter-spacing: 0.5px;
  }
  .card--back .wordmark {
    right: 27px; top: 158px;
    font-size: 25px;
    color: var(--ink-white);
  }

  .identity {
    position: absolute;
    right: 236px; top: 184px;
    text-align: right;
    color: var(--ink-white);
    white-space: nowrap;
  }
  .identity__name { font-size: 17px; font-weight: 600; line-height: 22px; }
  .identity__title { font-size: 12.5px; line-height: 18px; }

  .divider {
    position: absolute;
    left: 239px; top: 176px;
    width: 1px; height: 58px;
    background: var(--divider);
  }

  .contact {
    position: absolute;
    left: 256px; top: 180px;
    list-style: none;
    color: var(--ink-white);
    font-size: 11px;
  }
  .contact li {
    display: flex;
    align-items: center;
    height: 17.5px;
    white-space: nowrap;
  }
  .contact svg { width: 11px; height: 11px; margin-right: 7px; flex: none; }

  .back-url {
    position: absolute;
    right: 27px; top: 229px;
    font-size: 10.5px;
    font-style: italic;
    letter-spacing: 1px;
    color: var(--ink-white);
  }
</style>
</head>
<body>

<section class="card card--front" aria-label="Card front">
  <svg class="front-shape" viewBox="0 0 461 262" width="461" height="262" aria-hidden="true">
    <path d="M0,180 Q230,128 461,180 L461,262 L0,262 Z" fill="var(--brand-blue)"/>
    <path d="M0,178 Q230,124 461,178" fill="none" stroke="var(--brand-green)" stroke-width="3"/>
  </svg>

  <div class="wordmark">Qorvel Studies</div>

  <div class="identity">
    <p class="identity__name">Bertrand Okonfu</p>
    <p class="identity__title">VP Research &amp; Senior Analyst</p>
  </div>

  <div class="divider"></div>

  <ul class="contact">
    <li>
      <svg viewBox="0 0 12 12" aria-hidden="true"><path d="M2.5 0.8 L4.6 3.2 L3.5 4.6 Q4.6 7 7.2 8.4 L8.6 7.3 L11.2 9.4 L9.8 11.2 Q5.5 11 2.6 7.6 Q0.6 4.8 0.8 2.2 Z" fill="#fff"/></svg>
      555-203-4719
    </li>
    <li>
      <svg viewBox="0 0 12 12" aria-hidden="true"><rect x="0.5" y="2.5" width="11" height="7.5" fill="#fff"/><path d="M0.8 2.8 L6 6.8 L11.2 2.8" fill="none" stroke="var(--brand-blue)" stroke-width="1"/></svg>
      info@qorvelstudies.example
    </li>
    <li>
      <svg viewBox="0 0 12 12" aria-hidden="true"><circle cx="6" cy="6" r="5.5" fill="#fff"/><ellipse cx="6" cy="6" rx="2.3" ry="5.3" fill="none" stroke="var(--brand-blue)" stroke-width="0.9"/><path d="M0.7 6 H11.3" stroke="var(--brand-blue)" stroke-width="0.9"/></svg>
      www.qorvelstudies.example
    </li>
  </ul>
</section>

<section class="card card--back" aria-label="Card back">
  <div class="wordmark">Qorvel Studies</div>
  <p class="back-url">www.qorvelstudies.example</p>
</section>

</body>
</html>
```